Residential Remodeling Contractor needs updated business card

I need a new design for my business card.
Name of the company is Ridgefell Construction. I need a card that commands presence, strength, integrity. I have been in business for 28 years. I am a Residential Remodeling Contractor that covers all aspects of a residential remodel and build.

```html
<!DOCTYPE html>
<html lang="en">
<head>
<meta charset="utf-8">
<title>Ridgefell Construction – Business Card</title>
<link href="https://fonts.googleapis.com/css2?family=Montserrat:wght@400;500;700&display=swap" rel="stylesheet">
<style>
  :root {
    --navy: #213e80;
    --white: #ffffff;
    --ink: #1a1a1a;
    --soft-white: rgba(255,255,255,0.85);
    --divider: rgba(255,255,255,0.35);
    --backdrop: #e9e9ec;
  }
  * { margin: 0; padding: 0; box-sizing: border-box; }
  html, body { width: 1200px; height: 786px; overflow: hidden; }
  body {
    background: var(--backdrop);
    font-family: "Montserrat", sans-serif;
    position: relative;
  }
  .card {
    position: absolute;
    top: 238px;
    width: 540px;
    height: 310px;
    background: var(--navy);
    color: var(--white);
    overflow: hidden;
    box-shadow: 0 6px 18px rgba(0,0,0,0.18);
  }
  .card--front { left: 45px; }
  .card--back { left: 615px; }

  .wordmark {
    position: absolute;
    display: flex;
    align-items: center;
    gap: 10px;
    font-weight: 500;
    text-transform: uppercase;
    letter-spacing: 0.04em;
    line-height: 1.15;
    color: var(--white);
  }
  .wordmark__square {
    flex: none;
    background: var(--white);
  }
  .card--front .wordmark { left: 34px; top: 92px; font-size: 17px; }
  .card--front .wordmark__square { width: 14px; height: 14px; }
  .card--back .wordmark {
    left: 50%; top: 50%;
    transform: translate(-50%, -60%);
    font-size: 26px;
  }
  .card--back .wordmark__square { width: 20px; height: 20px; }

  .divider {
    position: absolute;
    left: 248px;
    top: 40px;
    width: 1px;
    height: 130px;
    background: var(--divider);
  }
  .person { position: absolute; left: 270px; top: 46px; }
  .person__name { font-weight: 700; font-size: 19px; }
  .person__role { font-size: 11px; color: var(--soft-white); margin-top: 3px; }

  .contacts {
    position: absolute;
    left: 270px;
    top: 112px;
    list-style: none;
    font-size: 11.5px;
  }
  .contacts li {
    display: flex;
    align-items: center;
    gap: 12px;
    height: 22px;
  }
  .contacts svg { width: 13px; height: 13px; flex: none; }

  .address-band {
    position: absolute;
    left: 0; right: 0;
    top: 228px;
    height: 42px;
    background: var(--white);
    color: var(--ink);
    font-size: 12.5px;
    display: flex;
    align-items: center;
    padding-left: 220px;
  }
</style>
</head>
<body>

  <section class="card card--front" aria-label="Business card, contact side">
    <div class="wordmark">
      <span class="wordmark__square"></span>
      <span>Ridgefell<br>Construction</span>
    </div>
    <div class="divider"></div>
    <div class="person">
      <div class="person__name">Daniel Hart</div>
      <div class="person__role">Owner</div>
    </div>
    <ul class="contacts">
      <li>
        <svg viewBox="0 0 16 16" aria-hidden="true"><path fill="#fff" d="M2 5c0-2 2-3 6-3s6 1 6 3v1.5h-3V5H5v1.5H2z M4 8h8l2 6H2z"/><circle cx="8" cy="11" r="1.6" fill="#213e80"/></svg>
        <span>555.014.2270</span>
      </li>
      <li>
        <svg viewBox="0 0 16 16" aria-hidden="true"><rect x="1" y="3" width="14" height="10" fill="#fff"/><path d="M1 3l7 6 7-6" fill="none" stroke="#213e80" stroke-width="1.3"/></svg>
        <span>info@ridgefellconstruction.com</span>
      </li>
      <li>
        <svg viewBox="0 0 16 16" aria-hidden="true"><circle cx="8" cy="8" r="7" fill="#fff"/><g fill="none" stroke="#213e80" stroke-width="1"><ellipse cx="8" cy="8" rx="3" ry="7"/><path d="M1 8h14M2.5 4.5h11M2.5 11.5h11"/></g></svg>
        <span>www.ridgefellconstruction.com</span>
      </li>
    </ul>
    <div class="address-band">42 Cedar Hollow Lane Brandon, MS 39042</div>
  </section>

  <section class="card card--back" aria-label="Business card, name side">
    <div class="wordmark">
      <span class="wordmark__square"></span>
      <span>Ridgefell<br>Construction</span>
    </div>
  </section>

</body>
</html>
```